Business Card Design - ChoiceCraft

Looking for creative, modern design, two sided for ChoiceCraft that is consistent with color and feel of website www.choicecraftpro.net.
Updates

Back of card will be used to promote products or have a quote revolving around decisions, change, leadership, innovation, creativity. Back should also have space to promote website, but optional to use the icon. Front of the card will need to use the icon and have standard place for name, job title, phone and email. We are not looking to put a mailing address or fax. Also want space to place a few words/phrase explaining what we do...such as individual growth and organizational development or tools, training, information...in addition, want the facebook icon small on the front somewhere as we are also on facebook.

Vector file uploaded of icon.

Target Market(s)

Professional coaching for individual growth and organizational development

Industry/Entity Type

Business

Requirements
Must have
• Icon...see attached.

```html
<!DOCTYPE html>
<html lang="en">
<head>
<meta charset="utf-8">
<title>ChoiceCraft Business Card</title>
<link rel="stylesheet" href="https://fonts.googleapis.com/css2?family=Saira:wght@400;700&family=Arimo:wght@400;700&display=swap">
<style>
  :root {
    --stage: #d9dadc;
    --card-white: #ffffff;
    --ink: #1b1b1b;
    --ink-soft: #333333;
    --rule: #b9b9b9;
    --blue-deep: #0a58a6;
    --blue-mid: #1677c8;
    --blue-light: #3aa6e6;
    --white: #ffffff;
    --mark-fill: #2a86d2;
    --mark-faint: rgba(255,255,255,0.22);
  }
  * { margin: 0; padding: 0; box-sizing: border-box; }
  html, body { width: 1200px; height: 1102px; overflow: hidden; }
  body { background: var(--stage); position: relative; font-family: "Saira", sans-serif; }

  .card {
    position: absolute;
    width: 793px;
    height: 453px;
    overflow: hidden;
    box-shadow: 0 2px 6px rgba(0,0,0,0.25);
  }
  .card--front { left: 75px; top: 63px; background: var(--card-white); }
  .card--back {
    left: 309px; top: 578px;
    background: radial-gradient(ellipse at 70% 55%, var(--blue-light) 0%, var(--blue-mid) 45%, var(--blue-deep) 100%);
  }

  /* Front */
  .brand { position: absolute; left: 40px; top: 46px; width: 300px; text-align: center; }
  .brand__disc {
    width: 160px; height: 160px; border-radius: 50%;
    background: var(--mark-fill); margin: 0 auto 38px;
  }
  .brand__name { font-weight: 700; font-size: 38px; color: var(--ink); letter-spacing: 0.5px; }

  .divider { position: absolute; left: 374px; top: 95px; width: 1px; height: 232px; background: var(--rule); }

  .contact { position: absolute; left: 400px; top: 108px; list-style: none; }
  .contact li { display: flex; align-items: center; font-size: 20px; line-height: 27px; color: var(--ink-soft); }
  .contact svg { width: 13px; height: 13px; margin-right: 8px; flex: none; }
  .contact .square { width: 12px; height: 12px; background: var(--blue-mid); margin-right: 9px; flex: none; }

  .tagline { position: absolute; left: 400px; top: 240px; font-size: 19px; line-height: 27px; color: var(--ink-soft); }

  .band {
    position: absolute; left: 0; bottom: 0; width: 793px; height: 76px;
    background: linear-gradient(90deg, var(--blue-deep) 0%, var(--blue-light) 55%, var(--blue-mid) 100%);
  }
  .band::before {
    content: ""; position: absolute; left: 0; top: -6px; width: 100%; height: 3px;
    background: var(--blue-mid);
  }

  .person { position: absolute; right: 24px; top: 398px; color: var(--white); }
  .person__name { font-weight: 700; font-size: 27px; }
  .person__title { font-size: 20px; }

  /* Back */
  .quotes { position: absolute; left: 50px; top: 40px; list-style: none; font-family: "Arimo", sans-serif; color: var(--white); }
  .quote { margin-bottom: 20px; }
  .quote__text { font-size: 19px; line-height: 30px; position: relative; padding-left: 24px; }
  .quote__text::before { content: "\201C"; position: absolute; left: 0; top: -6px; font-size: 34px; font-weight: 700; }
  .quote__text::after { content: "\201D"; font-size: 34px; font-weight: 700; vertical-align: -14px; margin-left: 2px; line-height: 0; }
  .quote__author { font-size: 19px; font-weight: 700; padding-left: 24px; line-height: 26px; }

  .back-mark {
    position: absolute; left: 548px; top: 252px;
    width: 136px; height: 136px; border-radius: 50%;
    background: var(--mark-faint);
    display: flex; align-items: center; justify-content: center;
  }
  .back-mark span { font-family: "Saira", sans-serif; font-weight: 700; font-size: 18px; color: var(--white); }
</style>
</head>
<body>

<section class="card card--front">
  <div class="brand">
    <div class="brand__disc"></div>
    <div class="brand__name">ChoiceCraft</div>
  </div>

  <div class="divider"></div>

  <ul class="contact">
    <li>
      <svg viewBox="0 0 16 16"><path d="M4 1h3l1 4-2 1c1 2 2 3 4 4l1-2 4 1v3c0 1-1 2-2 2C7 14 2 9 2 3c0-1 1-2 2-2z" fill="#333"/></svg>
      555-204-318
    </li>
    <li>
      <svg viewBox="0 0 16 16"><rect x="1" y="3" width="14" height="10" fill="#333"/><path d="M1 3l7 6 7-6" stroke="#fff" stroke-width="1.4" fill="none"/></svg>
      hello@choicecraftpro.net
    </li>
    <li>
      <svg viewBox="0 0 16 16"><circle cx="8" cy="8" r="6.5" fill="none" stroke="#333" stroke-width="1.5"/><path d="M1.5 8h13M8 1.5c-3 3-3 10 0 13M8 1.5c3 3 3 10 0 13" stroke="#333" stroke-width="1.2" fill="none"/></svg>
      www.choicecraftpro.net
    </li>
    <li>
      <span class="square"></span>
      /choicecraftpro
    </li>
  </ul>

  <p class="tagline">Coaching people toward growth<br>and teams toward lasting change.</p>

  <div class="band"></div>

  <div class="person">
    <span class="person__name">Your Name,</span>
    <span class="person__title">Title</span>
  </div>
</section>

<section class="card card--back">
  <ul class="quotes">
    <li class="quote">
      <p class="quote__text">Try not to become a man of success, but rather a man of value.</p>
      <p class="quote__author">- Marta Quillon</p>
    </li>
    <li class="quote">
      <p class="quote__text">The only constant is change.</p>
      <p class="quote__author">- Tobias Renn</p>
    </li>
    <li class="quote">
      <p class="quote__text">We are what we repeatedly do. Excellence is not an act, it is a habit.</p>
      <p class="quote__author">- Ivo Castell</p>
    </li>
    <li class="quote">
      <p class="quote__text">Simplicity is the ultimate sophistication.</p>
      <p class="quote__author">- Helena Okafor</p>
    </li>
    <li class="quote">
      <p class="quote__text">Life is not fair - get used to it.</p>
      <p class="quote__author">- Dale Pruitt</p>
    </li>
  </ul>

  <div class="back-mark"><span>ChoiceCraft</span></div>
</section>

</body>
</html>
```